MRT Property - Business Cards

Looking for a business card & general letterhead, signage etc design for our new logo.

Colours:
000a20
0056a2
00b5ef
0088ce
68cef2

Fonts:
Poppins
Karla

Please keep look and feel of new brand - example in the zip package I sent.

```html
<!DOCTYPE html>
<html lang="en">
<head>
<meta charset="utf-8">
<title>MRT Property – Letterhead</title>
<link rel="stylesheet" href="https://fonts.googleapis.com/css2?family=Poppins:wght@300;400;600&display=swap">
<style>
  :root {
    --ink: #000a20;
    --brand-deep: #0056a2;
    --brand-mid: #0088ce;
    --brand-bright: #00b5ef;
    --brand-light: #68cef2;
    --backdrop: #929196;
    --paper: #ffffff;
  }
  * { box-sizing: border-box; margin: 0; padding: 0; }
  html, body {
    width: 1200px;
    height: 792px;
    overflow: hidden;
    background: var(--backdrop);
    font-family: "Poppins", sans-serif;
  }
  .letterhead {
    position: absolute;
    left: 331px;
    top: 16px;
    width: 538px;
    height: 760px;
    background: var(--paper);
  }
  .brand {
    position: absolute;
    left: 76px;
    top: 52px;
    display: flex;
    align-items: center;
    gap: 8px;
  }
  .brand-dot {
    width: 18px;
    height: 18px;
    border-radius: 50%;
    background: var(--brand-mid);
  }
  .brand-name {
    font-family: "Poppins", sans-serif;
    font-weight: 600;
    font-size: 22px;
    line-height: 1;
    color: var(--brand-deep);
    letter-spacing: 0.2px;
  }
  .contact-rule {
    position: absolute;
    left: 339px;
    top: 21px;
    width: 1.6px;
    height: 104px;
    background: var(--brand-mid);
  }
  .contact {
    position: absolute;
    left: 356px;
    top: 25px;
    font-size: 11px;
    line-height: 13.5px;
  }
  .contact-list { list-style: none; }
  .contact-item {
    display: flex;
    align-items: center;
    gap: 4px;
    color: var(--ink);
    font-weight: 400;
  }
  .contact-icon {
    width: 6px;
    height: 8px;
    flex: none;
    fill: var(--brand-mid);
  }
  .address {
    display: flex;
    align-items: flex-start;
    gap: 4px;
    margin-top: 13px;
    color: var(--brand-mid);
    font-weight: 300;
    font-style: normal;
  }
  .address .contact-icon {
    width: 7px;
    height: 12px;
    margin-top: 1px;
  }
</style>
</head>
<body>
  <main class="letterhead">
    <div class="brand">
      <span class="brand-dot"></span>
      <span class="brand-name">MRT Property</span>
    </div>

    <div class="contact-rule"></div>

    <section class="contact">
      <ul class="contact-list">
        <li class="contact-item">
          <svg class="contact-icon" viewBox="0 0 10 10" aria-hidden="true"><path d="M2 0.5 L3.6 0.5 L4.2 3 L3 3.8 Q4 6 6.2 7 L7 5.8 L9.5 6.4 L9.5 8 Q9.5 9.5 8 9.5 Q0.5 9 0.5 2 Q0.5 0.5 2 0.5Z"/></svg>
          <span>+61 2 9418 5230</span>
        </li>
        <li class="contact-item">
          <svg class="contact-icon" viewBox="0 0 10 10" aria-hidden="true"><circle cx="5" cy="5" r="4.5" fill="none" stroke="var(--brand-mid)" stroke-width="1.2"/><ellipse cx="5" cy="5" rx="2" ry="4.5" fill="none" stroke="var(--brand-mid)" stroke-width="1"/><path d="M0.5 5 H9.5" stroke="var(--brand-mid)" stroke-width="1"/></svg>
          <span>www.mrtproperty.com.au</span>
        </li>
        <li class="contact-item">
          <svg class="contact-icon" viewBox="0 0 10 10" aria-hidden="true"><rect x="0.5" y="2" width="9" height="6.5" rx="0.8"/><path d="M1 2.6 L5 5.6 L9 2.6" fill="none" stroke="#fff" stroke-width="0.9"/></svg>
          <span>info@mrtproperty.com.au</span>
        </li>
      </ul>
      <address class="address">
        <svg class="contact-icon" viewBox="0 0 10 16" aria-hidden="true"><path d="M5 0.5 A4.5 4.5 0 0 1 9.5 5 Q9.5 8 5 13 Q0.5 8 0.5 5 A4.5 4.5 0 0 1 5 0.5Z M5 3 A2 2 0 1 0 5 7 A2 2 0 1 0 5 3Z" fill-rule="evenodd"/><path d="M2 14.8 H8" stroke="var(--brand-mid)" stroke-width="1"/></svg>
        <span>Suite 3.05, Tower 1<br>14 Lakeside Avenue, Sydney,<br>Riverbank Park NSW 2140</span>
      </address>
    </section>
  </main>
</body>
</html>
```